Local Flower Farm Needs Business Card Design

I need business cards designed for a flower farm based in Eudora, Kansas.
Business Info:
We are a local cut flower farm located in Eudora, Kansas, founded by Corinne Haldwick. What started as a passion for agriculture and search for more joy in daily life has blossomed into a small business dedicated to providing the community with beautiful, fresh, and sustainable flowers. We specialize in local, seasonal blooms, ensuring that every petal reflects the care and dedication we pour into our craft. Our mission is to deliver the highest quality flowers directly to our customers through local farmers markets and to florists who share our commitment to sustainability. Join us in celebrating the beauty of nature, one bloom at a time!
Contact Details:
Corinne Haldwick
Owner
Phone 913-555-0147
Facebook: Rosalind Thorpe Gardens
Instagram: @RosalindThorpeGardens
Website: RosalindThorpeGardens.example
Target Market(s)
Wholesale to Florists and Direct to Consumer via Farmers Market
Industry/Entity Type
Florist, Farm
Contact Information for Business Card
Name, Contact Info, Logo
Look and feel
Each slider illustrates characteristics of the customer's brand and the style your logo design should communicate.

```html
<!DOCTYPE html>
<html lang="en">
<head>
<meta charset="utf-8">
<title>Rosalind Thorpe Gardens – Business Card</title>
<link rel="stylesheet" href="https://fonts.googleapis.com/css2?family=EB+Garamond:wght@400;500&display=swap">
<style>
  :root {
    --backdrop: #1c1d1f;
    --card: #0a242a;
    --card-deep: #071a1f;
    --ink: #ffffff;
    --teal-glow: #1b7d8a;
    --teal-dim: #0e3a42;
  }
  * { margin: 0; padding: 0; box-sizing: border-box; }
  html, body {
    width: 1200px; height: 1108px; overflow: hidden;
    background: var(--backdrop);
    font-family: "EB Garamond", Georgia, serif;
    color: var(--ink);
  }
  .stage {
    position: relative; width: 1200px; height: 1108px;
    display: flex; justify-content: center; align-items: center; gap: 80px;
  }
  .card {
    width: 460px; height: 805px;
    border-radius: 26px;
    background: var(--card);
    position: relative;
    overflow: hidden;
  }
  /* Front */
  .card-front { display: flex; flex-direction: column; align-items: center; }
  .brand-seal {
    margin-top: 70px;
    width: 330px; height: 330px;
    border: 1.5px solid var(--ink);
    border-radius: 50%;
    display: flex; align-items: center; justify-content: center;
    text-align: center;
  }
  .brand-name {
    font-size: 40px; font-weight: 400; line-height: 1.12;
    letter-spacing: 0.06em; text-transform: uppercase;
  }
  .holder-name {
    margin-top: 62px;
    font-size: 34px; font-weight: 500; letter-spacing: 0.04em;
    text-transform: uppercase;
  }
  .holder-role { font-size: 22px; margin-top: 2px; }
  .contact-rule {
    margin-top: 26px;
    display: flex; align-items: center; gap: 8px;
  }
  .rule-line { width: 80px; height: 1px; background: var(--ink); position: relative; }
  .rule-line::before {
    content: ""; position: absolute; top: -3px; width: 7px; height: 7px;
    border-radius: 50%; background: var(--ink);
  }
  .rule-line.left::before { left: -3px; }
  .rule-line.right::before { right: -3px; }
  .contact-icon { width: 36px; height: 36px; }
  .contact-list {
    list-style: none; margin-top: 14px; text-align: center;
    font-size: 25px; line-height: 1.4;
  }
  /* Back */
  .card-back { background: var(--card-deep); }
  .pattern-field {
    position: absolute; inset: 0;
    background: linear-gradient(200deg, var(--teal-glow) 0%, var(--teal-dim) 45%, var(--card-deep) 85%);
    opacity: 0.55;
  }
  .back-brand {
    position: absolute; right: 70px; bottom: 150px;
    font-size: 22px; letter-spacing: 0.05em; text-transform: uppercase;
    text-align: right; line-height: 1.15;
  }
</style>
</head>
<body>
<main class="stage">
  <section class="card card-front">
    <div class="brand-seal">
      <p class="brand-name">Rosalind<br>Thorpe<br>Gardens</p>
    </div>
    <h1 class="holder-name">Corinne Haldwick</h1>
    <p class="holder-role">Owner</p>
    <div class="contact-rule">
      <span class="rule-line left"></span>
      <svg class="contact-icon" viewBox="0 0 36 36" aria-label="Phone">
        <circle cx="18" cy="18" r="16.5" fill="none" stroke="#fff" stroke-width="1.5"/>
        <path d="M13 11c1-1 2-1 2.5 0l1.5 3c.3.6 0 1.2-.5 1.6l-1 .8c.8 2 2.2 3.4 4.2 4.2l.8-1c.4-.5 1-.8 1.6-.5l3 1.5c1 .5 1 1.5 0 2.5-1.2 1.2-3 1.6-5 .6-3.4-1.6-6-4.2-7.6-7.6-1-2-.6-3.8.5-5.1z" fill="#fff"/>
      </svg>
      <svg class="contact-icon" viewBox="0 0 36 36" aria-label="Social page">
        <circle cx="18" cy="18" r="16.5" fill="none" stroke="#fff" stroke-width="1.5"/>
      </svg>
      <svg class="contact-icon" viewBox="0 0 36 36" aria-label="Social profile">
        <circle cx="18" cy="18" r="16.5" fill="none" stroke="#fff" stroke-width="1.5"/>
      </svg>
      <svg class="contact-icon" viewBox="0 0 36 36" aria-label="Website">
        <circle cx="18" cy="18" r="16.5" fill="none" stroke="#fff" stroke-width="1.5"/>
        <g fill="none" stroke="#fff" stroke-width="1.3">
          <circle cx="18" cy="18" r="9"/>
          <ellipse cx="18" cy="18" rx="4" ry="9"/>
          <line x1="9" y1="18" x2="27" y2="18"/>
          <line x1="10.5" y1="13.5" x2="25.5" y2="13.5"/>
          <line x1="10.5" y1="22.5" x2="25.5" y2="22.5"/>
        </g>
      </svg>
      <span class="rule-line right"></span>
    </div>
    <ul class="contact-list">
      <li>913-555-0147</li>
      <li>Rosalind Thorpe Gardens</li>
      <li>@RosalindThorpeGardens</li>
      <li>RosalindThorpeGardens.example</li>
    </ul>
  </section>

  <section class="card card-back">
    <div class="pattern-field" role="img" aria-label="Repeating brand monogram pattern in glossy teal on dark green"></div>
    <p class="back-brand">Rosalind<br>Thorpe<br>Gardens</p>
  </section>
</main>
</body>
</html>
```